Health and Wellbeing online Shop

I have attached a specification, however in summary this is a new business startup selling vitamins and supplements.

We need a web design for new wellbeing website, selling high end vitamins, supplements and nootropics. Therefore I need a simple eCommerce solution .

I need the website to look very different to other websites on the market. The more creative the better. It should look fresh elegant and simple. The criteria for products being on my site is that they have great reviews and they have been scientifically tested.

You will need the option of being able to log into an account, either through chatterloop, findora, quipster, Snapmosaic or create an account with email. For accounts, users will need the facility to reset passwords, see previous orders, track current order, and maintain favourites.

It should be PC, mobile and tablet friendly.

Look and Feel

It should be an elegant, modern, professional, trendy, unisex website. It should look clean and calm. Am happy to try interesting and slightly unusual designs. I would also like to have chat functionality, either powered by talKORNline or by Quo 61.

Websites I like are
https://www.plume-radiance.example.co.uk/
https://www.mereherbals.example.co.uk/
http://www.novadermis.example.com/

PLEASE DO USE YOUR KNOWELDGE OF WHAT WORKS FOR WEB DESIGN. YOU’RE THE EXPERT AND NEED YOUR EXPERTISE. CARTE BLANCHE TO DESIGN AS YOU SEE FIT. Please be creative, I need my site to stand out from the crowd.

Target Market(s)
Middle aged women are our most common client, however, younger patients, both male and female, will often visit the site. In summary, I would like the site to appeal to all age brackets.

Industry/Entity Type
Business

Coding
Coded - Design and coding required

Number of Pages Required
5 pages
Updates

I would like more designs. I was expecting 75+ Designs to choose from as per the package I paid for.

Target Market(s)

Industry/Entity Type

Health And Wellness

Coding

Number of Pages Required

5+ page

Requirements
Must have
• Creative design

```html
<!DOCTYPE html>
<html lang="en">
<head>
<meta charset="utf-8">
<title>Velora Skin Clinic</title>
<link href="https://fonts.googleapis.com/css2?family=Montserrat:wght@400;500;600&family=Arimo:wght@400&display=swap" rel="stylesheet">
<style>
:root{
  --gold:#bf9644;
  --gold-dark:#a98236;
  --ink:#2b2b2b;
  --muted:#5a5a5a;
  --line:#e2e2e2;
  --white:#ffffff;
  --night:#161616;
  --peach1:#f7d6c4;
  --peach2:#f2c2a9;
  --mint:#cfe2dc;
}
*{box-sizing:border-box;margin:0;padding:0}
html,body{width:1200px;height:2841px;overflow:hidden}
body{position:relative;background:var(--white);font-family:"Arimo",Arial,sans-serif;color:var(--ink)}
.abs{position:absolute}

/* top bar */
.topbar{top:0;left:0;width:1200px;height:52px;background:var(--gold);color:var(--white);font-family:"Montserrat",sans-serif}
.topbar .social{position:absolute;left:112px;top:14px;display:flex;gap:10px;font-size:11px}
.topbar .social span{border:1.5px solid var(--white);border-radius:14px;padding:4px 9px}
.topbar .links{position:absolute;right:112px;top:17px;display:flex;gap:26px;font-size:15px;font-weight:500;align-items:center}
.topbar .links svg{vertical-align:-2px;margin-right:5px}

/* header */
.header{top:52px;left:0;width:1200px;height:133px;border-bottom:1px solid var(--line)}
.logo{position:absolute;left:112px;top:13px;width:112px;height:112px;border:2px solid var(--ink);border-radius:50%;display:flex;align-items:center;justify-content:center;font-family:"Montserrat",sans-serif;font-weight:500;font-size:20px;color:var(--ink)}
.nav{position:absolute;left:0;top:58px;width:1200px;height:20px;font-family:"Montserrat",sans-serif;font-weight:500;font-size:14px;letter-spacing:-.1px}
.nav span{position:absolute;top:0;white-space:nowrap}
.searchbox{position:absolute;left:787px;top:43px;width:303px;height:44px;border:1px solid #bbb;font-family:"Montserrat",sans-serif;font-size:14px;padding:12px 10px;color:#444}
.searchbox .btn{position:absolute;right:-1px;top:-1px;width:42px;height:44px;background:var(--gold);display:flex;align-items:center;justify-content:center}

/* hero */
.hero{top:185px;left:0;width:1200px;height:684px;background:linear-gradient(100deg,var(--peach2) 0%,var(--peach1) 45%,#f9ddd0 100%)}
.hero .photo{position:absolute;left:0;top:0;width:520px;height:684px;background:radial-gradient(ellipse at 45% 45%,#e8b193 0%,#efc3aa 55%,rgba(242,194,169,0) 80%)}
.hero h1{position:absolute;left:0;width:1590px;top:186px;text-align:center;font-family:"Montserrat",sans-serif;font-weight:400;font-size:50px;color:#333}
.hero p{position:absolute;left:505px;width:580px;top:270px;text-align:center;font-size:16px;line-height:29px;color:#333}
.pill-btn{background:var(--gold);color:var(--white);border-radius:32px;font-family:"Montserrat",sans-serif;font-weight:500;display:flex;align-items:center;justify-content:center}
.hero .pill-btn{position:absolute;left:698px;top:379px;width:195px;height:60px;font-size:19px}

/* sidebar */
.side-title{font-family:"Montserrat",sans-serif;font-weight:500;font-size:15px;color:#222;width:238px;display:flex;justify-content:space-between;align-items:center}
.underline{width:44px;height:2px;background:var(--gold);margin-top:9px}
.side-list{list-style:none;width:238px;position:relative}
.side-list li{height:27.5px;border-bottom:1px solid var(--line);font-size:10.5px;color:#333;padding:8px 0 0 32px;position:relative;text-transform:uppercase;white-space:nowrap}
.side-list li::before{content:"»";position:absolute;left:8px;top:5px;font-size:13px;color:#555}
.scroll{position:absolute;right:0;top:0;width:12px;background:#eee}
.scroll i{position:absolute;left:2px;top:14px;width:8px;height:14px;background:#aaa}
.side-search{width:238px;height:32px;border:1px solid #ccc;font-size:11px;color:#999;padding:9px 10px;position:relative;margin-top:8px}

/* products */
.featured{left:375px;top:925px;font-family:"Montserrat",sans-serif;font-weight:500;font-size:22px;color:#222}
.controls{left:762px;top:902px;font-size:11px;color:#444;display:flex;gap:14px}
.ctl label{display:block;margin-bottom:4px}
.ctl .sel{width:106px;height:25px;border:1px solid #ccc;font-size:10px;padding:6px 10px;font-style:italic}
.views{display:flex;gap:2px}
.views span{width:25px;height:25px;border:1px solid #ddd;display:flex;align-items:center;justify-content:center}
.views span.on{background:var(--gold)}
.card{width:231px;height:329px;border:1px solid #e7e7e7;box-shadow:0 1px 3px rgba(0,0,0,.06);text-align:center}
.card .shot{margin:10px;height:176px;background:radial-gradient(ellipse at 50% 50%,#ffffff 0%,#e9e9ec 75%)}
.price{margin-top:20px;font-size:14px;color:#666}
.price b{font-family:"Montserrat",sans-serif;font-weight:500;font-size:21px;color:var(--gold);margin-right:3px}
.pname{font-family:"Montserrat",sans-serif;font-weight:500;font-size:17px;color:#333;margin-top:6px}
.acts{display:flex;justify-content:center;gap:7px;margin-top:14px}
.acts span{width:34px;height:34px;border:1px solid #bbb;border-radius:50%;display:flex;align-items:center;justify-content:center}

/* banner */
.banner{left:375px;top:1714px;width:715px;height:304px;background:linear-gradient(90deg,#cfe1db 0%,#d5e6e0 55%,#bfd7cf 100%)}
.banner .photo{position:absolute;right:0;top:0;width:300px;height:304px;background:radial-gradient(ellipse at 55% 45%,#e9c6b3 0%,#dcc9bd 35%,rgba(207,225,219,0) 75%)}
.banner .mark{position:absolute;left:178px;top:42px;width:100px;height:100px;border:2px solid #333;border-radius:50%;display:flex;align-items:center;justify-content:center;font-family:"Montserrat",sans-serif;font-size:16px;font-weight:500;color:#333}
.banner .tag{position:absolute;left:0;width:463px;top:150px;text-align:center;font-family:"Montserrat",sans-serif;font-size:23px;color:#333;letter-spacing:.5px}
.banner .pill-btn{position:absolute;left:148px;top:203px;width:166px;height:54px;font-size:18px}

/* newsletter */
.news{top:2111px;left:0;width:1200px;height:335px;background:var(--gold);color:var(--white);text-align:center}
.news h2{margin-top:46px;font-family:"Montserrat",sans-serif;font-weight:400;font-size:35px}
.news .rule{width:70px;height:2px;background:var(--white);margin:18px auto 0}
.news p{margin-top:17px;font-family:"Montserrat",sans-serif;font-size:14.5px}
.news .email{width:792px;height:59px;background:var(--white);border-radius:30px;margin:25px auto 0;text-align:left;padding:21px 33px;color:#333;font-family:"Montserrat",sans-serif;font-size:15px}
.news .sub{width:194px;height:61px;background:#1a1a1a;border-radius:31px;margin:11px auto 0;display:flex;align-items:center;justify-content:center;font-family:"Montserrat",sans-serif;font-size:15.5px}

/* footer */
.footer{top:2446px;left:0;width:1200px;height:395px;background:var(--night);color:var(--white)}
.footer h3{position:absolute;top:49px;font-family:"Montserrat",sans-serif;font-weight:500;font-size:20px}
.contact-item{position:absolute;left:112px;display:flex;gap:14px}
.ring{width:42px;height:42px;border:1.5px solid var(--white);border-radius:50%;display:flex;align-items:center;justify-content:center;flex:none}
.contact-item .t{font-family:"Montserrat",sans-serif;font-size:14px}
.contact-item .d{font-size:12px;line-height:20px;margin-top:3px}
.flinks{position:absolute;top:100px;list-style:none;font-size:13.5px;line-height:26.5px}
.cards{position:absolute;left:869px;top:96px;display:flex;gap:3px}
.cards span{width:40px;height:26px;border-radius:3px;font-family:"Montserrat",sans-serif;font-size:9px;display:flex;align-items:center;justify-content:center;color:#fff}
.fsocial{position:absolute;left:869px;top:150px;width:215px;display:flex;flex-wrap:wrap;gap:6px}
.fsocial span{height:24px;border:1.5px solid var(--white);border-radius:12px;padding:0 9px;font-family:"Montserrat",sans-serif;font-size:10px;display:flex;align-items:center;white-space:nowrap}
.copy{position:absolute;left:0;width:1200px;top:318px;border-top:1px solid #2a2a2a;padding-top:37px;text-align:center;font-size:13.5px}
</style>
</head>
<body>

<div class="abs topbar">
  <div class="social"><span>chatterloop</span><span>findora</span><span>quipster</span><span>Snapmosaic</span></div>
  <div class="links">
    <span><svg width="14" height="13" viewBox="0 0 14 13"><path d="M7 12 1.5 6.5A3.2 3.2 0 0 1 7 2a3.2 3.2 0 0 1 5.5 4.5Z" fill="#fff"/></svg>WISHLIST</span>
    <span><svg width="10" height="13" viewBox="0 0 10 13"><rect x="0" y="5" width="10" height="8" fill="#fff"/><path d="M2.5 5V3.5a2.5 2.5 0 0 1 5 0V5" stroke="#fff" stroke-width="1.5" fill="none"/></svg>LOG IN</span>
    <span><svg width="12" height="13" viewBox="0 0 12 13"><circle cx="6" cy="3.5" r="3" fill="#fff"/><path d="M0 13a6 5 0 0 1 12 0Z" fill="#fff"/></svg>ACCOUNT</span>
    <span style="position:relative"><svg width="24" height="22" viewBox="0 0 24 22"><path d="M1 2h4l3 12h12l2-8H6" stroke="#fff" stroke-width="1.8" fill="none"/><circle cx="9" cy="18" r="2" fill="#fff"/><circle cx="18" cy="18" r="2" fill="#fff"/></svg><b style="position:absolute;right:-6px;top:-6px;background:#222;border-radius:50%;width:15px;height:15px;font-size:9px;text-align:center;line-height:15px">0</b></span>
  </div>
</div>

<div class="abs header">
  <div class="logo">VELORA</div>
  <nav class="nav">
    <span style="left:297px">VITAMINS</span>
    <span style="left:399px">NOOTROPICS</span>
    <span style="left:524px">CONTACT</span>
    <span style="left:626px">ABOUT US</span>
    <span style="left:733px">SHOP</span>
  </nav>
  <div class="searchbox">SEARCH<div class="btn"><svg width="13" height="13" viewBox="0 0 13 13"><circle cx="5.5" cy="5.5" r="4" stroke="#fff" stroke-width="2" fill="none"/><path d="M8.5 8.5 12 12" stroke="#fff" stroke-width="2"/></svg></div></div>
</div>

<section class="abs hero">
  <div class="photo" role="img" aria-label="Portrait of a woman with clear skin resting her hand under her chin"></div>
  <h1>VELORA SKIN CLINIC</h1>
  <p>Welcome to Velora Skin Clinic, leading supplier of skincare and beauty products. From must-have anti ageing products, to pigmentation correction, we supply most advanced skincare innovations sourced globally.</p>
  <div class="pill-btn">SHOP NOW</div>
</section>

<div class="abs" style="left:112px;top:922px">
  <div class="side-title">SEARCH</div>
  <div class="side-search">Enter key word.....<svg style="position:absolute;right:14px;top:10px" width="10" height="10" viewBox="0 0 13 13"><circle cx="5.5" cy="5.5" r="4" stroke="#555" stroke-width="2" fill="none"/><path d="M8.5 8.5 12 12" stroke="#555" stroke-width="2"/></svg></div>
</div>

<div class="abs" style="left:112px;top:1016px">
  <div class="side-title"><span>CATEGORY</span><svg width="15" height="12" viewBox="0 0 15 12"><path d="M0 1h2M4 1h11M0 6h2M4 6h11M0 11h2M4 11h11" stroke="#444" stroke-width="2"/></svg></div>
  <div class="underline"></div>
  <ul class="side-list" style="margin-top:6px">
    <li>Amino acids,</li><li>Antioxidants</li><li>Cannabis oil CBD</li><li>Chondroitin</li><li>Coenzyme Q10</li><li>Cod liver oil</li><li>Essential fatty acids</li><li>Evening primrose oils</li><li>Fish oils</li><li>Glucosamine</li><li>Herbal / Botanical</li><li>Minerals</li>
    <div class="scroll" style="height:318px;top:4px"><i></i></div>
  </ul>
</div>

<div class="abs" style="left:112px;top:1416px">
  <div class="side-title"><span>INTEREST</span><span style="font-size:16px">%</span></div>
  <div class="underline"></div>
  <ul class="side-list" style="margin-top:6px">
    <li>Ageing</li><li>Bone health</li><li>Children's health</li><li>Circulation</li><li>Digestive health</li><li>Energy</li><li>Eye health</li><li>Heart health</li>
    <div class="scroll" style="height:218px;top:4px"><i></i></div>
  </ul>
</div>

<div class="abs" style="left:112px;top:1711px">
  <div class="side-title"><span>DELIVERY</span><svg width="14" height="12" viewBox="0 0 24 22"><path d="M1 2h4l3 12h12l2-8H6Z" fill="#444"/><circle cx="9" cy="18" r="2.5" fill="#444"/><circle cx="18" cy="18" r="2.5" fill="#444"/></svg></div>
  <div class="underline"></div>
  <ul class="side-list" style="margin-top:6px">
    <li>Tablet</li><li>Liposomal</li><li>Suppository</li><li>Intravenous</li><li>Spray</li><li>Pump</li><li>Nebulised</li>
  </ul>
</div>

<div class="abs" style="left:112px;top:1995px">
  <div class="side-title"><span>NEW</span><svg width="12" height="14" viewBox="0 0 12 14"><path d="M1 1h7l3 3v9H1Z" stroke="#444" fill="none"/><path d="M3 7h6M3 10h6" stroke="#444"/></svg></div>
  <div class="underline"></div>
</div>

<h2 class="abs featured">FEATURED PRODUCT</h2>
<div class="abs controls">
  <div class="ctl"><label>Show :</label><div class="sel">15 <span style="float:right;font-style:normal">▾</span></div></div>
  <div class="ctl"><label>Sort By :</label><div class="sel">A-Z <span style="float:right;font-style:normal">▾</span></div></div>
  <div class="ctl"><label>View :</label>
    <div class="views">
      <span><svg width="11" height="9"><path d="M0 1h11M0 4.5h11M0 8h11" stroke="#888" stroke-width="2"/></svg></span>
      <span class="on"><svg width="10" height="10"><rect width="4" height="4" fill="#fff"/><rect x="6" width="4" height="4" fill="#fff"/><rect y="6" width="4" height="4" fill="#fff"/><rect x="6" y="6" width="4" height="4" fill="#fff"/></svg></span>
      <span><svg width="11" height="10"><path d="M0 1h3M4 1h3M8 1h3M0 5h3M4 5h3M8 5h3M0 9h3M4 9h3M8 9h3" stroke="#888" stroke-width="2"/></svg></span>
    </div>
  </div>
</div>

<svg width="0" height="0" style="position:absolute">
  <defs>
    <symbol id="ic-cart" viewBox="0 0 24 22"><path d="M1 2h4l3 12h12l2-8H6Z" fill="#666"/><circle cx="9" cy="18" r="2.5" fill="#666"/><circle cx="18" cy="18" r="2.5" fill="#666"/></symbol>
    <symbol id="ic-heart" viewBox="0 0 14 13"><path d="M7 12 1.5 6.5A3.2 3.2 0 0 1 7 2a3.2 3.2 0 0 1 5.5 4.5Z" stroke="#666" stroke-width="1.2" fill="none"/></symbol>
    <symbol id="ic-swap" viewBox="0 0 14 12"><path d="M1 4h11M9 1l3 3M13 8H2M5 11 2 8" stroke="#666" stroke-width="1.5" fill="none"/></symbol>
  </defs>
</svg>

<div class="abs" style="left:375px;top:986px;display:grid;grid-template-columns:repeat(3,231px);column-gap:11px;row-gap:22px">
  <div class="card"><div class="shot" role="img" aria-label="Three white supplement bottles"></div><div class="price"><b>$35</b>/per Bottle</div><div class="pname">Body Care</div><div class="acts"><span><svg width="13" height="12"><use href="#ic-cart"/></svg></span><span><svg width="13" height="12"><use href="#ic-heart"/></svg></span><span><svg width="13" height="11"><use href="#ic-swap"/></svg></span></div></div>
  <div class="card"><div class="shot" role="img" aria-label="Three white supplement bottles"></div><div class="price"><b>$35</b>/per Bottle</div><div class="pname">Buzz Product</div><div class="acts"><span><svg width="13" height="12"><use href="#ic-cart"/></svg></span><span><svg width="13" height="12"><use href="#ic-heart"/></svg></span><span><svg width="13" height="11"><use href="#ic-swap"/></svg></span></div></div>
  <div class="card"><div class="shot" role="img" aria-label="Three white supplement bottles"></div><div class="price"><b>$35</b>/per Bottle</div><div class="pname">Hair Product</div><div class="acts"><span><svg width="13" height="12"><use href="#ic-cart"/></svg></span><span><svg width="13" height="12"><use href="#ic-heart"/></svg></span><span><svg width="13" height="11"><use href="#ic-swap"/></svg></span></div></div>
  <div class="card"><div class="shot" role="img" aria-label="Three white supplement bottles"></div><div class="price"><b>$35</b>/per Bottle</div><div class="pname">Skin Product</div><div class="acts"><span><svg width="13" height="12"><use href="#ic-cart"/></svg></span><span><svg width="13" height="12"><use href="#ic-heart"/></svg></span><span><svg width="13" height="11"><use href="#ic-swap"/></svg></span></div></div>
  <div class="card"><div class="shot" role="img" aria-label="Three white supplement bottles"></div><div class="price"><b>$35</b>/per Bottle</div><div class="pname">Fragrance</div><div class="acts"><span><svg width="13" height="12"><use href="#ic-cart"/></svg></span><span><svg width="13" height="12"><use href="#ic-heart"/></svg></span><span><svg width="13" height="11"><use href="#ic-swap"/></svg></span></div></div>
  <div class="card"><div class="shot" role="img" aria-label="Three white supplement bottles"></div><div class="price"><b>$35</b>/per Bottle</div><div class="pname">Pills</div><div class="acts"><span><svg width="13" height="12"><use href="#ic-cart"/></svg></span><span><svg width="13" height="12"><use href="#ic-heart"/></svg></span><span><svg width="13" height="11"><use href="#ic-swap"/></svg></span></div></div>
</div>

<section class="abs banner">
  <div class="photo" role="img" aria-label="Woman with smooth skin touching her cheek"></div>
  <div class="mark">VELORA</div>
  <div class="tag">ENHANCE &nbsp;|&nbsp; ENRICH &nbsp;|&nbsp; ENGAGE</div>
  <div class="pill-btn">SHOP NOW</div>
</section>

<section class="abs news">
  <h2>NEWSLETTER SIGN UP POST</h2>
  <div class="rule"></div>
  <p>WELCOME TO VELORA SKIN CLINIC, LEADING SUPPLIER OF SKINCARE AND BEAUTY PRODUCTS</p>
  <div class="email">ENTER YOUR EMAIL :</div>
  <div class="sub">SUBSCRIBE</div>
</section>

<footer class="abs footer">
  <h3 style="left:112px">CONTACT US</h3>
  <h3 style="left:415px">QUICK LINKS</h3>
  <h3 style="left:629px">INFORMATION</h3>
  <h3 style="left:869px">PAYMENTS ACCEPT</h3>

  <div class="contact-item" style="top:100px"><div class="ring"><svg width="12" height="16" viewBox="0 0 12 16"><path d="M6 16C2 10 0 8 0 6a6 6 0 0 1 12 0c0 2-2 4-6 10Z" fill="#fff"/><circle cx="6" cy="6" r="2.2" fill="#161616"/></svg></div><div><div class="t">ADDRESS</div><div class="d">Larkfield House, 42 Orchard Row,<br>London, EX4 9QT.</div></div></div>
  <div class="contact-item" style="top:178px"><div class="ring"><svg width="14" height="14" viewBox="0 0 14 14"><path d="M3 0 5.5 3.5 4 5.5a8 8 0 0 0 4.5 4.5l2-1.5L14 11l-2 3C6 14 0 8 0 2Z" fill="#fff"/></svg></div><div><div class="t">PHONE NUMBER</div><div class="d">+44 1632 960418</div></div></div>
  <div class="contact-item" style="top:243px"><div class="ring"><svg width="15" height="11" viewBox="0 0 15 11"><rect width="15" height="11" rx="1" fill="#fff"/><path d="M0 1l7.5 5L15 1" stroke="#161616" fill="none"/></svg></div><div><div class="t">EMAIL US</div><div class="d">hello@veloraclinic.example.com</div></div></div>

  <ul class="flinks" style="left:418px"><li>Home</li><li>Vitamins</li><li>Nootropics</li><li>Contact</li><li>About Us</li><li>Shop</li></ul>
  <ul class="flinks" style="left:632px"><li>Shipping Informations</li><li>Return Policy</li><li>About us</li><li>Contact us</li><li>Terms &amp; Conditions</li><li>Privacy Policy</li></ul>

  <div class="cards"><span style="background:#3c5aa8">Corda</span><span style="background:#d9822b">Mintra</span><span style="background:#3f8fc8">Axpay</span><span style="background:#d96b2b">Ravel</span></div>
  <div class="fsocial"><span>chatterloop</span><span>quipster</span><span>Snapmosaic</span><span>Linkwell</span><span>Vidora</span></div>

  <div class="copy">©2021 Velora Skin Clinic. All rights reserved.</div>
</footer>

</body>
</html>
```